Meridian Crestline Motors *

Professional business cards for our auto wholesale dealership.

Target Market(s)

New and used cars sales managers and middle class to higher end private party buyers.

Industry/Entity Type

Automotive

Contact Information for Business Card

Meridian Crestline Motors
Darnell R Okonski
Owner
(555) 304-6618
mercrestmotors@quillbox.example
Dealer Lic # 48265

Logo Text

Meridian Crestline Motors, Mer Crest Motors, MCM, etc

Font styles to use
Serif
Sans Serif

Colors

Designer to choose colors to be used in the design.

Requirements
Must have
• A professional, but not pretentious, look
Nice to have
• It might be nice to see "MCM" in a shape form i.e. circle, triangle, etc in the corner or background somehwere
Should not have
• bright "girly" colors

```html
<!DOCTYPE html>
<html lang="en">
<head>
<meta charset="utf-8">
<title>Meridian Crestline Motors – Business Cards</title>
<link href="https://fonts.googleapis.com/css2?family=Open+Sans:wght@400;600;700&display=swap" rel="stylesheet">
<style>
  :root {
    --backdrop: #3a3b3d;
    --card: #252a31;
    --card-light: #2e343c;
    --lime: #9ccc18;
    --lime-deep: #7fae0c;
    --white: #ffffff;
    --muted: #d9dde2;
  }
  * { box-sizing: border-box; margin: 0; padding: 0; }
  html, body {
    width: 1200px; height: 1200px; overflow: hidden;
    background: var(--backdrop);
    font-family: "Open Sans", Arial, sans-serif;
  }
  .stage {
    position: relative; width: 1200px; height: 1200px;
    display: flex; flex-direction: column; align-items: center; justify-content: center; gap: 80px;
  }
  .card {
    position: relative; width: 760px; height: 434px;
    border-radius: 22px; overflow: hidden;
    background: radial-gradient(circle at 45% 40%, var(--card-light), var(--card) 75%);
    box-shadow: 0 14px 30px rgba(0,0,0,.45);
  }
  .card__band {
    position: absolute; left: 0; right: 0; bottom: 0; height: 30px;
    background: linear-gradient(90deg, var(--lime), var(--lime-deep));
  }
  .card__band::before {
    content: ""; position: absolute; left: 0; right: 0; top: -16px; height: 6px;
    background: var(--lime);
  }

  /* front */
  .front__mark {
    position: absolute; left: 70px; top: 110px; width: 170px; height: 170px;
    border-radius: 50%; background: var(--lime);
    box-shadow: 0 0 0 6px var(--card), 0 0 0 9px var(--lime);
  }
  .front__name {
    position: absolute; left: 272px; top: 128px;
    color: var(--white); font-weight: 700; font-size: 40px; line-height: 1.15;
    text-transform: uppercase; letter-spacing: .5px;
  }

  /* back */
  .back__company {
    position: absolute; left: 60px; top: 38px;
    color: var(--white); font-weight: 700; font-size: 26px; text-transform: uppercase;
  }
  .back__rule {
    position: absolute; left: 0; right: 0; top: 198px; height: 3px; background: var(--lime);
  }
  .back__mark {
    position: absolute; left: 520px; top: 100px; width: 200px; height: 200px;
    border-radius: 50%; background: var(--lime);
    box-shadow: 0 0 0 6px var(--card), 0 0 0 9px var(--lime);
  }
  .person {
    position: absolute; left: 60px; top: 118px;
    padding-left: 20px; border-left: 8px solid var(--lime);
    color: var(--white);
  }
  .person__name { font-size: 26px; font-weight: 600; line-height: 1.15; }
  .person__role { font-size: 17px; color: var(--muted); }
  .contact {
    position: absolute; left: 60px; top: 224px; list-style: none;
    color: var(--muted); font-size: 16px; line-height: 1.9;
  }
  .contact li { display: flex; align-items: center; gap: 10px; }
  .contact svg { width: 16px; height: 16px; flex: none; }
  .contact .licence { padding-left: 0; }
</style>
</head>
<body>
<main class="stage">
  <section class="card card--front" aria-label="Business card front">
    <div class="front__mark"></div>
    <h1 class="front__name">Meridian Crestline<br>Motors</h1>
    <div class="card__band"></div>
  </section>

  <section class="card card--back" aria-label="Business card back">
    <p class="back__company">Meridian Crestline Motors</p>
    <div class="back__rule"></div>
    <div class="back__mark"></div>
    <div class="person">
      <p class="person__name">Darnell R Okonski</p>
      <p class="person__role">Owner</p>
    </div>
    <ul class="contact">
      <li>
        <svg viewBox="0 0 24 24" aria-hidden="true"><path fill="#9ccc18" d="M6.6 10.8a15.1 15.1 0 0 0 6.6 6.6l2.2-2.2a1 1 0 0 1 1-.25 11.4 11.4 0 0 0 3.6.57 1 1 0 0 1 1 1V20a1 1 0 0 1-1 1A17 17 0 0 1 3 4a1 1 0 0 1 1-1h3.5a1 1 0 0 1 1 1c0 1.25.2 2.45.57 3.57a1 1 0 0 1-.25 1z"/></svg>
        (555) 304-6618
      </li>
      <li>
        <svg viewBox="0 0 24 24" aria-hidden="true"><rect x="2.5" y="5" width="19" height="14" rx="1.5" fill="none" stroke="#9ccc18" stroke-width="2"/><path d="M3 6l9 7 9-7" fill="none" stroke="#9ccc18" stroke-width="2"/></svg>
        mercrestmotors@quillbox.example
      </li>
      <li class="licence">Dealer Lic # 48265</li>
    </ul>
    <div class="card__band"></div>
  </section>
</main>
</body>
</html>
```